Billiards 50th Anniversary Calendar

Need a custom calendar designed to finish at 8.5 x 11. and to be supplied as a pdf print file including .25 bleed on all sides. Total is 24 pages. I will supply one image per calendar month. Cover to have a collage of monthly images or samples of some of your favorites incorporated with a cool design that transitions throughout the calendar. The client's 50th Anniversary logo must be incorporated into the design.

Back cover has a group image to be incorporated as well.

Target Market(s)

Calendar is selling to their billiard clients

Industry/Entity Type

Male dominant industry

Requirements
Must have
• Must have a design element that continues through the calendar but flows with the images well. One image per calendar month.

```html
<!DOCTYPE html>
<html lang="en">
<head>
<meta charset="utf-8">
<title>CueCraft Billiards 50th Anniversary Calendar – January 2022</title>
<link href="https://fonts.googleapis.com/css2?family=Montserrat:wght@300;400;600;700&display=swap" rel="stylesheet">
<style>
  :root {
    --backdrop: #e4d6bd;
    --paper: #ffffff;
    --navy: #1f3d74;
    --grey: #b3b3b3;
    --label-grey: #8d8d8d;
    --ink: #2b2b2b;
    --sunday-red: #d9262c;
    --orange: #ef8a1c;
    --green: #2f6434;
    --photo-dark: #0d1014;
    --photo-felt: #2f95d6;
  }
  * { margin: 0; padding: 0; box-sizing: border-box; }
  html, body {
    width: 960px; height: 1200px; overflow: hidden;
    background: var(--backdrop);
    font-family: "Montserrat", sans-serif;
  }
  .canvas { position: relative; width: 960px; height: 1200px; }

  .month-photo {
    position: absolute; left: 145px; top: 68px; width: 670px; height: 518px;
    background: linear-gradient(180deg, var(--photo-dark) 0%, #141a22 58%, #1d5f8e 74%, var(--photo-felt) 100%);
  }

  .calendar-page {
    position: absolute; left: 145px; top: 614px; width: 670px; height: 518px;
    background: var(--paper);
  }
  .calendar-page .side-photo {
    position: absolute; right: 0; top: 0; width: 162px; height: 470px;
    background: linear-gradient(180deg, var(--photo-dark) 0%, #17120d 45%, #5a4127 75%, var(--photo-felt) 100%);
  }
  .calendar-page .band-orange {
    position: absolute; left: 0; bottom: 0; width: 508px; height: 48px; background: var(--orange);
  }
  .calendar-page .band-green {
    position: absolute; right: 0; bottom: 0; width: 162px; height: 48px; background: var(--green);
  }

  .brand {
    position: absolute; left: 36px; top: 50px; width: 110px;
    display: flex; align-items: center; gap: 6px;
    color: var(--green); font-weight: 700; font-size: 15px; line-height: 1.1;
  }
  .brand .brand-dot {
    flex: none; width: 14px; height: 14px; border-radius: 50%; background: var(--orange);
  }

  .month-title {
    position: absolute; right: 217px; top: 48px; text-align: right;
  }
  .month-title .month {
    display: block; color: var(--navy); font-weight: 400; font-size: 41px; letter-spacing: 1px; line-height: 1;
  }
  .month-title .year {
    display: block; color: var(--grey); font-weight: 300; font-size: 38px; line-height: 1; margin-top: 3px;
  }

  .month-grid {
    position: absolute; left: 36px; top: 167px; width: 423px;
    display: grid; grid-template-columns: repeat(7, 1fr);
    text-align: center;
  }
  .month-grid .weekday {
    font-size: 8px; font-weight: 600; color: var(--label-grey); letter-spacing: 0.2px; height: 20px;
  }
  .month-grid .weekday.sun { color: var(--sunday-red); }
  .month-grid .day {
    font-size: 28px; font-weight: 300; color: var(--ink); height: 55px; line-height: 1;
    padding-top: 6px;
  }
  .month-grid .day.sun { color: var(--sunday-red); }
</style>
</head>
<body>
<main class="canvas">
  <div class="month-photo" role="img" aria-label="Month photo: woman in polka-dot dress and red heels posing on a blue pool table with cue, rack and balls in a dark billiards hall"></div>

  <section class="calendar-page">
    <div class="brand"><span class="brand-dot"></span><span>CueCraft Billiards</span></div>

    <h1 class="month-title">
      <span class="month">JANUARY</span>
      <span class="year">2022</span>
    </h1>

    <div class="month-grid">
      <div class="weekday sun">SUNDAY</div>
      <div class="weekday">MONDAY</div>
      <div class="weekday">TUESDAY</div>
      <div class="weekday">WEDNESDAY</div>
      <div class="weekday">THURSDAY</div>
      <div class="weekday">FRIDAY</div>
      <div class="weekday">SATURDAY</div>

      <div class="day"></div><div class="day"></div><div class="day"></div><div class="day"></div><div class="day"></div><div class="day"></div>
      <div class="day sun">1</div>

      <div class="day sun">2</div><div class="day">3</div><div class="day">4</div><div class="day">5</div><div class="day">6</div><div class="day">7</div><div class="day">8</div>
      <div class="day sun">9</div><div class="day">10</div><div class="day">11</div><div class="day">12</div><div class="day">13</div><div class="day">14</div><div class="day">15</div>
      <div class="day sun">16</div><div class="day">17</div><div class="day">18</div><div class="day">19</div><div class="day">20</div><div class="day">21</div><div class="day">24</div>
      <div class="day sun">25</div><div class="day">26</div><div class="day">27</div><div class="day">28</div><div class="day">29</div><div class="day">30</div><div class="day"></div>
    </div>

    <div class="side-photo" role="img" aria-label="Side photo: woman in leopard-print jumpsuit and red scarf seated by a pool table holding the eight ball"></div>
    <div class="band-orange"></div>
    <div class="band-green"></div>
  </section>
</main>
</body>
</html>
```